MRT Property - Business Cards

Looking for a business card & general letterhead, signage etc design for our new logo.

Colours:
000a20
0056a2
00b5ef
0088ce
68cef2

Fonts:
Poppins
Karla

Please keep look and feel of new brand - example in the zip package I sent.

```html
<!DOCTYPE html>
<html lang="en">
<head>
<meta charset="utf-8">
<title>MRT Property – Business Cards</title>
<link href="https://fonts.googleapis.com/css2?family=Poppins:wght@300;400;500;700;800&display=swap" rel="stylesheet">
<style>
  :root {
    --navy: #0c1330;
    --ink: #000a20;
    --blue-deep: #0056a2;
    --blue-mid: #0088ce;
    --blue-bright: #00b5ef;
    --blue-soft: #68cef2;
    --white: #ffffff;
    --backdrop: #3a3b3e;
  }
  * { box-sizing: border-box; margin: 0; padding: 0; }
  html, body { width: 1200px; height: 900px; overflow: hidden; }
  body {
    background: var(--backdrop);
    font-family: "Poppins", sans-serif;
    position: relative;
  }
  .card {
    position: absolute;
    left: 250px;
    width: 700px;
    height: 400px;
    border-radius: 22px;
    overflow: hidden;
    box-shadow: 0 14px 30px rgba(0,0,0,.45);
  }
  .card--back { top: 30px; background: var(--navy); }
  .card--front { top: 470px; background: var(--navy); }

  .wordmark {
    font-family: "Poppins", sans-serif;
    font-weight: 800;
    letter-spacing: 1px;
    line-height: 1;
    display: flex;
    align-items: center;
    gap: 14px;
  }
  .wordmark__dot {
    width: 18px; height: 18px; border-radius: 50%;
    flex: none;
  }
  .card--back .wordmark {
    position: absolute; right: 56px; top: 200px;
    color: var(--white); font-size: 52px;
  }
  .card--back .wordmark__dot { background: var(--blue-bright); }

  .front__top {
    position: absolute; left: 0; top: 0; width: 100%; height: 190px;
    background: var(--white);
    border-bottom: 3px solid var(--blue-bright);
    display: flex; align-items: center; justify-content: center;
  }
  .front__top .wordmark { color: var(--blue-deep); font-size: 56px; }
  .front__top .wordmark__dot { background: var(--blue-bright); }

  .person {
    position: absolute; left: 54px; top: 250px; width: 250px; text-align: right;
  }
  .person__name {
    color: var(--blue-bright); font-weight: 800; font-size: 30px; line-height: 1.1;
    text-transform: uppercase;
  }
  .person__role { color: var(--white); font-weight: 300; font-size: 17px; margin-top: 4px; }

  .divider {
    position: absolute; left: 330px; top: 225px; width: 2px; height: 130px;
    background: var(--blue-bright);
  }
  .contact {
    position: absolute; left: 356px; top: 222px;
    color: var(--white); font-weight: 300; font-size: 17px; line-height: 1.5;
    list-style: none;
  }
  .contact li { display: flex; align-items: center; gap: 8px; }
  .contact svg { width: 14px; height: 14px; flex: none; }
  .contact__address { margin-top: 4px; }
</style>
</head>
<body>
  <section class="card card--back" aria-label="Business card, back">
    <div class="wordmark"><span class="wordmark__dot"></span>MRT PROPERTY</div>
  </section>

  <section class="card card--front" aria-label="Business card, front">
    <div class="front__top">
      <div class="wordmark"><span class="wordmark__dot"></span>MRT PROPERTY</div>
    </div>

    <div class="person">
      <p class="person__name">Dana Whitlow</p>
      <p class="person__role">Founder &amp; Principal</p>
    </div>

    <div class="divider"></div>

    <ul class="contact">
      <li>
        <svg viewBox="0 0 24 24" aria-hidden="true"><path fill="#00b5ef" d="M6.6 10.8a15 15 0 006.6 6.6l2.2-2.2a1 1 0 011-.25 11.4 11.4 0 003.6.57 1 1 0 011 1V20a1 1 0 01-1 1A17 17 0 013 4a1 1 0 011-1h3.5a1 1 0 011 1c0 1.25.2 2.45.57 3.57a1 1 0 01-.25 1z"/></svg>
        +1- 415-555-0192
      </li>
      <li>
        <svg viewBox="0 0 24 24" aria-hidden="true"><rect x="2" y="5" width="20" height="14" rx="2" fill="none" stroke="#00b5ef" stroke-width="2"/><path d="M3 6l9 7 9-7" fill="none" stroke="#00b5ef" stroke-width="2"/></svg>
        info@mrtproperty.com
      </li>
      <li>
        <svg viewBox="0 0 24 24" aria-hidden="true"><circle cx="12" cy="12" r="10" fill="none" stroke="#00b5ef" stroke-width="2"/><path d="M2 12h20M12 2c3 3 3 17 0 20M12 2c-3 3-3 17 0 20" fill="none" stroke="#00b5ef" stroke-width="1.6"/></svg>
        www.mrtproperty.com
      </li>
      <li class="contact__address">4820 North Elm Avenue</li>
      <li>#27, Suite Lakeview Park</li>
    </ul>
  </section>
</body>
</html>
```